Business cards for Zestcycle

We need a business card layout for our new bike and e-bike rental (we also sell used e-bikes and bike accessories). The logo already exists.

```html
<!DOCTYPE html>
<html lang="en">
<head>
<meta charset="utf-8">
<title>Zestcycle Business Cards</title>
<link href="https://fonts.googleapis.com/css2?family=Open+Sans:wght@400;600;700&display=swap" rel="stylesheet">
<style>
  :root {
    --bg: #e6e8e9;
    --ink: #1d3338;
    --deep: #1e363c;
    --mint: #5cc3a6;
    --white: #ffffff;
  }
  * { box-sizing: border-box; margin: 0; padding: 0; }
  html, body {
    width: 1200px; height: 782px; overflow: hidden;
    background: var(--bg);
    font-family: "Open Sans", sans-serif;
  }
  .stage {
    position: relative; width: 1200px; height: 782px;
    display: flex; align-items: center; justify-content: center; gap: 40px;
  }
  .card {
    position: relative; width: 540px; height: 309px;
    box-shadow: 0 10px 30px rgba(0,0,0,0.18);
    overflow: hidden;
  }
  /* Front */
  .card--front { background: var(--white); color: var(--ink); }
  .person { position: absolute; left: 34px; top: 34px; }
  .person__name { font-size: 17px; font-weight: 600; letter-spacing: 0.5px; text-transform: uppercase; }
  .person__name .accent { color: var(--mint); }
  .person__role { font-size: 12.5px; margin-top: 1px; }
  .contacts { position: absolute; left: 34px; top: 150px; list-style: none; font-size: 13.5px; line-height: 20px; }
  .contacts li { display: flex; align-items: center; gap: 8px; }
  .contacts svg { width: 11px; height: 11px; fill: var(--ink); flex: none; }
  .brand { position: absolute; right: 40px; top: 112px; text-align: center; }
  .brand__name { font-size: 44px; font-weight: 400; color: var(--mint); letter-spacing: 4px; line-height: 1; }
  .brand__tagline { font-size: 12.5px; font-weight: 700; margin-top: 8px; }
  .address { position: absolute; right: 40px; top: 216px; font-size: 14px; line-height: 19px; text-align: right; }
  .bands { position: absolute; left: 0; bottom: 0; width: 540px; height: 40px; }
  /* Back */
  .card--back { background: var(--deep); }
  .pattern { position: absolute; inset: 0; background: linear-gradient(135deg, #213c42, #1c343a); }
  .back__brand {
    position: absolute; right: 90px; bottom: 78px;
    font-size: 30px; font-weight: 400; letter-spacing: 3px; color: var(--white);
  }
</style>
</head>
<body>
<main class="stage">
  <section class="card card--front" aria-label="Business card front">
    <div class="person">
      <p class="person__name">Marlen <span class="accent">Voss</span></p>
      <p class="person__role">Managing Director</p>
    </div>
    <ul class="contacts">
      <li><svg viewBox="0 0 12 12"><path d="M2.5 1h2l1 3-1.5 1a7 7 0 0 0 3 3l1-1.5 3 1v2a1 1 0 0 1-1 1A10 10 0 0 1 1.5 2a1 1 0 0 1 1-1z"/></svg>044-123 456 789</li>
      <li><svg viewBox="0 0 12 12"><path d="M3.5 0h5a1 1 0 0 1 1 1v10a1 1 0 0 1-1 1h-5a1 1 0 0 1-1-1V1a1 1 0 0 1 1-1zM4 1.5v7.5h4V1.5z"/></svg>044-123 456 789</li>
      <li><svg viewBox="0 0 12 12"><path d="M0 2h12v8H0zm1 1v.4l5 3.2 5-3.2V3z"/></svg>info@webname.com</li>
      <li><svg viewBox="0 0 12 12"><path d="M6 0a6 6 0 1 0 0 12A6 6 0 0 0 6 0zm0 1.2a4.8 4.8 0 0 1 0 9.6 4.8 4.8 0 0 1 0-9.6zM3 5h6v2H3z"/></svg>www.websitename.com</li>
    </ul>
    <div class="brand">
      <p class="brand__name">ZESTCYCLE</p>
      <p class="brand__tagline">ride light, ride far</p>
    </div>
    <p class="address">12345, Address Goes Here<br>Country Name, 123456</p>
    <svg class="bands" viewBox="0 0 540 40" preserveAspectRatio="none" aria-hidden="true">
      <polygon points="0,8 262,8 246,40 0,40" fill="var(--deep)"/>
      <polygon points="272,14 540,14 540,40 252,40" fill="var(--mint)"/>
    </svg>
  </section>

  <section class="card card--back" aria-label="Business card back">
    <div class="pattern" role="img" aria-label="Faint repeating pattern of the brand symbol across the card"></div>
    <p class="back__brand">ZESTCYCLE</p>
  </section>
</main>
</body>
</html>
```